Business Card for a New Zealand IT Startup

I need a business card for VELTA Holdings. We are a young startup based in New Zealand working in internet marketing and web development. The design should have some element connected to New Zealand, such as wave, koru or silver fern, just don't use a kiwi bird.

```html
<!DOCTYPE html>
<html lang="en">
<head>
<meta charset="utf-8">
<title>VELTA Holdings – Business Card</title>
<link rel="stylesheet" href="https://fonts.googleapis.com/css2?family=Open+Sans:ital@1&family=Roboto:ital,wght@0,400;0,700;1,300&display=swap">
<style>
  :root {
    --page: #ffffff;
    --brand-blue: #1a6fb4;
    --label-blue: #2a6fb0;
    --card-grey: #e4e4e6;
    --fern-shadow: #cfd0d2;
    --koru-tone: #3a6fa0;
    --white: #ffffff;
  }
  * { margin: 0; padding: 0; box-sizing: border-box; }
  html, body {
    width: 1200px;
    height: 1200px;
    overflow: hidden;
    background: var(--page);
  }
  .sheet {
    position: relative;
    width: 1200px;
    height: 1200px;
  }
  .side-label {
    position: absolute;
    left: 0;
    width: 1200px;
    text-align: center;
    font-family: "Open Sans", sans-serif;
    font-style: italic;
    font-size: 20px;
    color: var(--label-blue);
  }
  .side-label--front { top: 134px; }
  .side-label--back { top: 1042px; }

  .card {
    position: absolute;
    left: 248px;
    width: 704px;
    height: 422px;
    overflow: hidden;
  }
  .card--front {
    top: 166px;
    background: var(--card-grey);
  }
  .card--back {
    top: 604px;
    background: var(--brand-blue);
    color: var(--white);
    font-family: "Roboto", sans-serif;
  }

  .fern-backdrop {
    position: absolute;
    inset: 0;
    background:
      radial-gradient(ellipse 60% 40% at 35% 20%, var(--fern-shadow), transparent 70%),
      radial-gradient(ellipse 40% 30% at 85% 15%, var(--fern-shadow), transparent 70%),
      var(--card-grey);
  }

  .wordmark {
    position: absolute;
    left: 0;
    right: 0;
    top: 108px;
    text-align: center;
    font-family: "Roboto", sans-serif;
    font-weight: 700;
    color: var(--brand-blue);
  }
  .wordmark__name {
    display: block;
    font-size: 150px;
    line-height: 140px;
    letter-spacing: 2px;
  }
  .wordmark__tagline {
    display: block;
    margin-top: 14px;
    font-size: 38px;
    line-height: 44px;
    letter-spacing: 27px;
    padding-left: 27px;
  }

  .koru-backdrop {
    position: absolute;
    left: 46px;
    top: 152px;
    width: 186px;
    height: 270px;
    border-radius: 50% 50% 20% 40%;
    background: radial-gradient(ellipse at 55% 35%, var(--koru-tone), transparent 72%);
    opacity: 0.8;
  }

  .person {
    position: absolute;
    left: 0;
    right: 0;
    text-align: center;
  }
  .person__name {
    top: 96px;
    font-weight: 700;
    font-size: 62px;
    line-height: 72px;
  }
  .person__role {
    top: 166px;
    font-weight: 300;
    font-style: italic;
    font-size: 32px;
    line-height: 38px;
  }

  .contact {
    position: absolute;
    left: 0;
    right: 0;
    top: 282px;
    list-style: none;
    font-size: 18px;
    line-height: 24px;
    text-align: center;
  }
  .contact__item {
    display: flex;
    justify-content: center;
    align-items: center;
    gap: 10px;
  }
  .contact__item--web { margin-top: 12px; }
  .contact__icon {
    width: 18px;
    height: 18px;
    fill: var(--white);
  }
</style>
</head>
<body>
<main class="sheet">
  <p class="side-label side-label--front">front</p>

  <section class="card card--front">
    <div class="fern-backdrop" role="img" aria-label="Faded photograph of silver fern fronds"></div>
    <h1 class="wordmark">
      <span class="wordmark__name">VELTA</span>
      <span class="wordmark__tagline">HOLDINGS</span>
    </h1>
  </section>

  <section class="card card--back">
    <div class="koru-backdrop" role="img" aria-label="Faint photograph of an unfurling koru fern frond"></div>
    <h2 class="person person__name">John Smith</h2>
    <p class="person person__role">company position</p>
    <ul class="contact">
      <li class="contact__item">
        <svg class="contact__icon" viewBox="0 0 24 24" aria-hidden="true"><path d="M6.6 10.8a15.1 15.1 0 0 0 6.6 6.6l2.2-2.2a1 1 0 0 1 1-.25 11.4 11.4 0 0 0 3.6.57 1 1 0 0 1 1 1V20a1 1 0 0 1-1 1A17 17 0 0 1 3 4a1 1 0 0 1 1-1h3.5a1 1 0 0 1 1 1c0 1.25.2 2.45.57 3.6a1 1 0 0 1-.25 1z"/></svg>
        <span>0800-372915</span>
      </li>
      <li class="contact__item">
        <svg class="contact__icon" viewBox="0 0 24 24" aria-hidden="true"><path d="M2 5h20v14H2z M3.5 6.5 12 13l8.5-6.5" fill="none" stroke="#ffffff" stroke-width="0"/><path d="M2 5h20v14H2V5zm1.8 1.2L12 12.4l8.2-6.2H3.8zM3.2 7.3v10.5h17.6V7.3L12 14 3.2 7.3z"/></svg>
        <span>johnsmith@veltaholdings.com</span>
      </li>
      <li class="contact__item contact__item--web">
        <span>www.yourwebsite.com</span>
      </li>
    </ul>
  </section>

  <p class="side-label side-label--back">back</p>
</main>
</body>
</html>
```